Packaging Design job - Product : Supplement for Travel Sickness

We need a packaging design for a travel sickness supplement called "VORELIX"

VORELIX It is a dietary supplement based on ginger which has properties fighting against motion sickness.

Ginger is a root used for many years for its beneficial effects on health. In addition to its stimulating and toning properties which help to resist fatigue, ginger is used as an adjuvant in case of nausea, vomiting and motion sickness. Ideal for pregnant women to combat certain disadvantages of pregnancy.

This product will be in blister form of 30 capsules. We need for this a packaging design for the box.Dimensions: 100 * 20 * 200 mm

We would like to see clean, modern and fresh designs.This should give the impression of professional products of pharmaceutical quality. You will also find attached the logo of our company.Ps : You can change the color of the logo

Mention to put on the box :

• Produit en France: Laboratoire KALDUNE, 24 Rue des Glaïeuls 37390 VERNOUX
• Distribué au Maroc: SORALUMIN 17 rue Ibn Zaydoun 30050 FEZ MAROC
• Complément alimentaire, ce n'est pas un médicament
• Voie orale
• Tenir hors de portée des enfants
• Respectez la dose recommandée
• Ce produit ne remplace pas une alimentation variée

Mode d'utilisation (How to use) :

2 à 3 gélules 30 min avant de prendre le véhicule de transport
1 gélule par jour en cas de cure

Font styles to use
Serif
Sans Serif
Script

Requirements
Should not have
• Sales and other "must buy" "guaranteed" etc

```html
<!DOCTYPE html>
<html lang="fr">
<head>
<meta charset="utf-8">
<title>VORELIX – boîte 30 capsules</title>
<link rel="stylesheet" href="https://fonts.googleapis.com/css2?family=Quicksand:wght@300;400&family=Lato:ital,wght@0,400;0,700;1,400&family=Arimo:wght@400;700&display=swap">
<style>
  :root {
    --olive: #767860;
    --peach: #f7d0a3;
    --ink: #4a4a4a;
    --dark: #2f2f2f;
    --paper: #ffffff;
    --cut: #555555;
  }
  html, body { margin: 0; padding: 0; width: 1159px; height: 1200px; overflow: hidden; background: var(--paper); }
  .dieline { display: block; width: 1159px; height: 1200px; }
  .cut { fill: none; stroke: var(--cut); stroke-width: 0.8; }
  .band-olive { fill: var(--olive); }
  .band-peach { fill: var(--peach); }
  .band-white { fill: var(--paper); }
  .brand { font-family: "Quicksand", sans-serif; font-weight: 300; fill: var(--ink); }
  .legal { font-family: "Lato", sans-serif; font-style: italic; font-size: 8px; fill: var(--dark); }
  .lorem { font-family: "Lato", sans-serif; font-weight: 700; font-size: 8px; fill: var(--dark); }
  .notice { font-family: "Arimo", sans-serif; font-size: 13px; fill: var(--dark); }
  .usage-title { font-family: "Arimo", sans-serif; font-weight: 700; font-size: 13px; fill: var(--dark); }
  .usage-text { font-family: "Arimo", sans-serif; font-size: 13.5px; fill: var(--dark); }
  .usage-frame { fill: var(--paper); stroke: var(--ink); stroke-width: 1.6; }
  .route-label { font-family: "Quicksand", sans-serif; font-weight: 300; font-size: 26px; fill: var(--paper); }
  .claim { font-family: "Lato", sans-serif; font-size: 16.5px; fill: var(--dark); }
  .count { font-family: "Lato", sans-serif; font-size: 18px; fill: var(--paper); }
  .barcode-zone { fill: none; stroke: #111; stroke-width: 1.2; }
  .ginger-visual { fill: url(#gingerTone); }
</style>
</head>
<body>
<svg class="dieline" viewBox="0 0 960 994" xmlns="http://www.w3.org/2000/svg">
  <defs>
    <radialGradient id="gingerTone" cx="45%" cy="45%" r="60%">
      <stop offset="0%" stop-color="#f2d68a"/>
      <stop offset="60%" stop-color="#c9a068"/>
      <stop offset="100%" stop-color="#8fae5a"/>
    </radialGradient>
    <clipPath id="backPanel"><rect x="112" y="133" width="726" height="364"/></clipPath>
    <clipPath id="frontPanel"><rect x="112" y="565" width="726" height="368"/></clipPath>
  </defs>

  <!-- side flaps -->
  <g class="flaps">
    <g class="flaps-left">
      <path class="cut" d="M112,62 L48,76 V118 L112,132"/>
      <path class="cut" d="M112,138 C80,138 50,140 48,168 V468 C50,494 80,496 112,496"/>
      <path class="cut" d="M112,500 L48,514 V554 L112,564"/>
      <path class="cut" d="M112,570 C80,570 50,572 48,600 V902 C50,930 80,932 112,932"/>
    </g>
    <g class="flaps-right" transform="translate(950,0) scale(-1,1)">
      <path class="cut" d="M112,62 L48,76 V118 L112,132"/>
      <path class="cut" d="M112,138 C80,138 50,140 48,168 V468 C50,494 80,496 112,496"/>
      <path class="cut" d="M112,500 L48,514 V554 L112,564"/>
      <path class="cut" d="M112,570 C80,570 50,572 48,600 V902 C50,930 80,932 112,932"/>
    </g>
  </g>

  <!-- top flap -->
  <g class="top-flap">
    <rect class="barcode-zone" x="155" y="70" width="228" height="50"/>
    <g transform="rotate(180 475 97)">
      <text class="brand" x="160" y="114" font-size="42">VORELIX</text>
      <text class="legal" x="380" y="96">Complément alimentaire,</text>
      <text class="legal" x="380" y="107">ce n'est pas un médicament</text>
    </g>
  </g>

  <!-- back panel -->
  <g class="back-panel" clip-path="url(#backPanel)">
    <rect class="band-olive" x="112" y="133" width="726" height="364"/>
    <path class="band-peach" d="M112,320 C300,190 600,160 838,172 V497 H112 Z"/>
    <path class="band-white" d="M112,410 C300,240 600,195 838,205 V497 H112 Z"/>
  </g>
  <path class="usage-frame" d="M165,205 V400 Q165,440 205,440 H343 Q383,440 383,400 V205"/>
  <ellipse class="ginger-visual" cx="275" cy="228" rx="95" ry="60" role="img" aria-label="Racine de gingembre fraîche avec tranches et feuilles vertes"/>
  <g class="back-copy" transform="rotate(180 475 287)">
    <text class="usage-title" x="676" y="176" text-anchor="middle">Mode d'utilisation</text>
    <text class="usage-text" x="676" y="208" text-anchor="middle">2 à 3 gélules 30 min avant de</text>
    <text class="usage-text" x="676" y="226" text-anchor="middle">prendre le véhicule de transport</text>
    <text class="usage-text" x="676" y="246" text-anchor="middle">1 gélule par jour en cas de cure</text>

    <g class="warnings">
      <circle cx="214" cy="162" r="2.5" fill="#2f2f2f"/>
      <text class="notice" x="224" y="166">Tenir hors de portée des enfants</text>
      <circle cx="214" cy="181" r="2.5" fill="#2f2f2f"/>
      <text class="notice" x="224" y="185">Respectez la dose recommandée</text>
      <circle cx="214" cy="199" r="2.5" fill="#2f2f2f"/>
      <text class="notice" x="224" y="203">Ce produit ne remplace pas une alimentation variée</text>
    </g>
    <g class="addresses">
      <text class="notice" x="210" y="235">Produit en France:</text>
      <text class="notice" x="210" y="254">Laboratoire KALDUNE,</text>
      <text class="notice" x="210" y="273">24 Rue des Glaïeuls 37390 VERNOUX</text>
      <text class="notice" x="210" y="300">Distribué au Maroc:</text>
      <text class="notice" x="210" y="318">SORALUMIN 17 rue Ibn Zaydoun</text>
      <text class="notice" x="210" y="336">30050 FEZ MAROC</text>
    </g>
  </g>

  <!-- side strip -->
  <g class="side-strip">
    <text class="brand" x="160" y="553" font-size="42">VORELIX</text>
    <text class="legal" x="378" y="540">Complément alimentaire,</text>
    <text class="legal" x="378" y="551">ce n'est pas un médicament</text>
    <text class="lorem" x="651" y="528" text-anchor="middle">Lorem ipsum dolor sit amet, consectetuer adipiscing elit, sed diam nonummy nibh</text>
    <text class="lorem" x="651" y="538.5" text-anchor="middle">euismod tincidunt ut laoreet dolore magna aliquam erat volutpat. Ut wisi enim ad</text>
    <text class="lorem" x="651" y="549" text-anchor="middle">minim veniam, quis nostrud exerci tation ullamcorper suscipit lobortis nisl ut aliquip ex</text>
    <text class="lorem" x="651" y="559.5" text-anchor="middle">ea commodo consequat. Duis autem vel eum iriure dolor in hendrerit in vulputate</text>
  </g>

  <!-- front panel -->
  <g class="front-panel" clip-path="url(#frontPanel)">
    <rect class="band-white" x="112" y="565" width="726" height="368"/>
    <path class="band-peach" d="M112,878 C420,900 700,820 838,662 V933 H112 Z"/>
    <path class="band-olive" d="M112,905 C420,918 700,850 838,700 V933 H112 Z"/>
  </g>
  <g class="route-tag">
    <path class="band-olive" d="M676,570 H792 V702 L676,750 Z"/>
    <text class="route-label" x="734" y="641" text-anchor="middle">Voie</text>
    <text class="route-label" x="734" y="670" text-anchor="middle">orale</text>
  </g>
  <text class="brand" x="156" y="752" font-size="100">VORELIX</text>
  <g class="claim-ribbon">
    <path class="band-peach" d="M162,762 H583 L577,795 H158 Z"/>
    <text class="claim" x="172" y="784">Complément alimentaire, ce n'est pas un médicament</text>
  </g>
  <text class="count" x="810" y="906" text-anchor="end">30 Capsules</text>

  <!-- panel outline and folds -->
  <g class="folds">
    <rect class="cut" x="112" y="60" width="726" height="873"/>
    <line class="cut" x1="112" y1="133" x2="838" y2="133"/>
    <line class="cut" x1="112" y1="497" x2="838" y2="497"/>
    <line class="cut" x1="112" y1="565" x2="838" y2="565"/>
  </g>
</svg>
</body>
</html>
```